Website Redesign for an Appointment Setting and Lead Generation Company.

I need to redesign an existing website. The website that we are looking to be redesigned is www.farlinqo.com. FarLinqo is a B2B appointment setting organization. The idea is to present a modern look website for professional services company. The idea is to engage the user, look at various services and generate more inbound leads for the website

Target Market(s)

US, APAC, Europe, UK. Focused on B2B companies more than $100 Mn

Industry/Entity Type

Professional Service

Number of Pages Required

5+ page

Font styles to use
Other font styles liked:
• Roboto

Requirements
Must have
• Home Page - Banner Image, Section for Client testimonials
Industry Page - To show industry capabilities
Services Page - To show service capabilities
Blogs Page - to show blogs
Offerings Page - Offerings Page
Nice to have
• I would like to have a elegant design with small animation. Preferably use colors from the logo attached. Use infographics where possible

```html
<!DOCTYPE html>
<html lang="en">
<head>
<meta charset="utf-8">
<title>FarLinqo – Build your Sales Pipeline</title>
<link href="https://fonts.googleapis.com/css2?family=Roboto:wght@300;400;500;700&display=swap" rel="stylesheet">
<style>
:root{
  --red:#d23a3a;
  --red-dark:#b22a2a;
  --ink:#1b1b1b;
  --text:#333;
  --muted:#777;
  --line:#e2e2e2;
  --navy:#1c2738;
  --footer:#0b0b0b;
  --white:#fff;
}
*{margin:0;padding:0;box-sizing:border-box}
html,body{width:1200px;height:4390px;overflow:hidden}
body{font-family:'Roboto',sans-serif;color:var(--text);background:var(--white);position:relative}
/* header */
.site-header{position:absolute;left:0;top:0;width:1200px;height:87px;background:var(--white)}
.brand{position:absolute;left:90px;top:18px;display:flex;align-items:center;gap:10px}
.brand-mark{width:30px;height:30px;background:var(--red)}
.brand-name{font-size:32px;font-weight:500;color:var(--red);line-height:1}
.brand-tag{position:absolute;left:200px;top:50px;font-size:15px;font-weight:400;color:var(--text)}
.nav{position:absolute;top:32px;left:586px;display:flex;font-size:15px}
.nav a{color:var(--muted);text-decoration:none;margin-right:48px}
.nav a.active{color:var(--red)}
.nav-search{position:absolute;left:1093px;top:34px}
/* hero */
.hero{position:absolute;left:0;top:87px;width:1200px;height:573px;
  background:radial-gradient(ellipse at 60% 60%,#8a6c66 0%,#4d5878 35%,#2f4a82 65%,#1f2f5a 100%)}
.hero h1{position:absolute;top:185px;width:1200px;text-align:center;color:var(--white);font-size:45px;font-weight:500}
.hero p{position:absolute;top:255px;left:150px;width:900px;text-align:center;color:var(--white);font-size:16px;line-height:27px}
.btn{display:block;background:var(--red);color:var(--white);text-align:center;border-radius:24px;font-weight:500}
.hero .btn{position:absolute;left:517px;top:330px;width:166px;height:46px;line-height:46px;font-size:16px}
/* offering */
.section-title{position:absolute;width:1200px;text-align:center;font-size:31px;font-weight:500;color:var(--ink);line-height:37px}
.offer-intro{position:absolute;left:146px;top:845px;width:908px;text-align:justify;text-align-last:center;font-size:15px;line-height:29.6px;color:#666}
.card{position:absolute;top:1045px;width:335px;height:428px;border:1px solid var(--line);background:var(--white)}
.card-media{position:absolute;left:5px;top:5px;width:323px;height:193px}
.card h3{position:absolute;top:209px;width:100%;text-align:center;font-size:21px;font-weight:500;color:var(--ink)}
.card p{position:absolute;top:245px;left:16px;width:301px;font-size:14px;line-height:28px;color:#666;text-align:justify;text-align-last:center}
/* stats */
.stats{position:absolute;left:0;top:1569px;width:1200px;height:781px;
  background:linear-gradient(180deg,#1e2a3c 0%,#243247 45%,#1a2433 100%)}
.stats .section-title{color:var(--white);top:93px}
.stat{position:absolute;width:300px;text-align:center;color:var(--white)}
.stat-ring{width:178px;height:178px;margin:0 auto;border:2px solid var(--red);border-radius:50%;display:flex;align-items:center;justify-content:center;font-size:45px;font-weight:500}
.stat-label{margin-top:14px;font-size:16px;line-height:26px}
/* testimonials */
.avatar{position:absolute;left:547px;top:2499px;width:106px;height:106px;border-radius:50%;background:radial-gradient(circle at 50% 40%,#d9c2b0,#8b8b8b)}
.quote{position:absolute;left:150px;top:2628px;width:900px;text-align:center;font-size:16px;line-height:29.5px;color:#666}
.quote-by{position:absolute;top:2756px;width:1200px;text-align:center;font-size:15px;font-weight:500;color:var(--ink)}
.arrow{position:absolute;top:2666px}
/* regions */
.regions{position:absolute;left:0;top:2875px;width:1200px;height:588px;
  background:linear-gradient(120deg,#c43434 0%,#b93030 45%,#9c2424 100%)}
.regions .section-title{color:var(--white);top:100px}
.region{position:absolute;top:217px;width:306px;height:306px;border-radius:50%;text-align:center;color:var(--white);padding-top:60px}
.region.dark{background:#1c0f0f}
.region.light{background:#d34848}
.region h4{font-size:23px;font-weight:500;margin-bottom:12px}
.region p{font-size:15px;line-height:29px}
/* leads */
.lead{position:absolute;top:3616px;width:200px;text-align:center}
.lead b{display:block;font-size:35px;font-weight:500;color:var(--red)}
.lead span{display:block;font-size:17px;color:var(--ink);margin-top:2px}
/* footer */
.site-footer{position:absolute;left:0;top:3782px;width:1200px;height:608px;background:var(--footer);color:var(--white)}
.foot-col{position:absolute;top:85px}
.foot-col h5{font-size:16px;font-weight:700;margin-bottom:34px}
.foot-col li{list-style:none;font-size:14px;height:37px;padding-left:28px;position:relative}
.foot-col li::before{content:"›";position:absolute;left:0;top:-3px;font-size:17px}
.field{position:absolute;left:803px;width:307px;height:42px;background:var(--white);border:1px solid #ccc;font-size:13px;color:#888;padding:12px 10px}
.foot-col.form{left:803px}
.site-footer .btn{position:absolute;left:805px;top:441px;width:150px;height:45px;line-height:45px;font-size:16px}
.copyright{position:absolute;top:573px;width:1200px;text-align:center;font-size:12px;color:#ccc}
.page-code{position:absolute;left:1148px;top:575px;font-size:12px;color:#ccc}
</style>
</head>
<body>

<header class="site-header">
  <div class="brand"><span class="brand-mark"></span><span class="brand-name">FarLinqo</span></div>
  <div class="brand-tag">Reach Further</div>
  <nav class="nav">
    <a class="active">Home</a><a>Industry</a><a>Services</a><a>Blogs</a><a>Offerings</a>
  </nav>
  <svg class="nav-search" width="16" height="16" viewBox="0 0 16 16"><circle cx="6.5" cy="6.5" r="5" fill="none" stroke="#777" stroke-width="2"/><line x1="10.5" y1="10.5" x2="15" y2="15" stroke="#777" stroke-width="2"/></svg>
</header>

<section class="hero" role="img" aria-label="Business handshake over a network graphic and stock chart">
  <h1>Build your Sales Pipeline in the New Normal!</h1>
  <p>Providing end-to-end webinar management services - including platform support, audience acquisition, providing subject matter expert speakers, webinar moderation, reporting, and lead nurturing on the webinar attendees</p>
  <a class="btn">Know More</a>
</section>

<h2 class="section-title" style="top:754px">Offering Dynamic Solutions for your<br>Niche Product Offerings</h2>
<p class="offer-intro">Ranked amongst the best B2B lead generation companies globally we have our presence across North America, Europe, APAC and India. Our experienced and trained lead generation executives understand your unique service offerings and work along your campaign journey to achieve the desired goals. Leveraging our extensive proprietary database, we target key decision-makers &amp; influencers across industries. Our sales lead generation services are custom-made for your service offerings, be it next-generation technologies like machine learning, digital transformation, analytics, and artificial intelligence. We work as an extension of your team and deliver results that matter to your business – Improve Sales Pipeline and Acquire New Customers.</p>

<article class="card" style="left:89px">
  <div class="card-media" role="img" aria-label="Team meeting around a table with charts" style="background:linear-gradient(135deg,#b5b0a8,#6f6a63)"></div>
  <h3>Global Partner</h3>
  <p>With Delivery Locations Across 4 Countries, FarLinqo Is One Of The Top Lead Generation Companies Serving More Than 17 Countries Across The Globe. We Are Today Partner To 9 Of The Top 12 It Companies And 30 Of The Top 50 Tier 1 It / Ites Companies</p>
</article>
<article class="card" style="left:433px">
  <div class="card-media" role="img" aria-label="Hand touching web domain icons" style="background:linear-gradient(135deg,#16406e,#3a7fb8)"></div>
  <h3>Domain Expertise</h3>
  <p>15,000+ Campaigns Executed Across 12 Verticals And 100+ Service Lines For Offerings Across Business Process Management, Technology Services, Machine Learning, Robotic Process Management, Artificial Intelligence And Many More</p>
</article>
<article class="card" style="left:776px">
  <div class="card-media" role="img" aria-label="Business people in front of glass office towers" style="background:linear-gradient(135deg,#9fc3dd,#2f5f86)"></div>
  <h3>Proprietary Systems</h3>
  <p>Our unique &amp; proprietary Call FOCUS Model, powered by in house researched database of more than 750K Influencers and Decision makers enables us to reach out to your targeted clients to setup appointments</p>
</article>

<section class="stats" role="img" aria-label="Looking up at dark skyscrapers">
  <h2 class="section-title">Let your Sales Team focus on Closures with<br>our B2B Lead Generation Services</h2>
  <div class="stat" style="left:128px;top:195px"><div class="stat-ring">3800</div><div class="stat-label">Research Reports Generated</div></div>
  <div class="stat" style="left:450px;top:195px"><div class="stat-ring">80%</div><div class="stat-label">Client Retention Rate</div></div>
  <div class="stat" style="left:772px;top:195px"><div class="stat-ring">500+</div><div class="stat-label">Surveys and Interviews<br>conducted per month</div></div>
  <div class="stat" style="left:128px;top:444px"><div class="stat-ring">50%</div><div class="stat-label">Leads Generated<br>with CXOs &amp; VPs</div></div>
  <div class="stat" style="left:450px;top:444px"><div class="stat-ring">33</div><div class="stat-label">Events Managed</div></div>
  <div class="stat" style="left:772px;top:444px"><div class="stat-ring">20</div><div class="stat-label">Databases Subscribed</div></div>
</section>

<h2 class="section-title" style="top:2440px">Client Testimonials</h2>
<div class="avatar" role="img" aria-label="Client portrait photo"></div>
<svg class="arrow" style="left:52px" width="36" height="36" viewBox="0 0 36 36"><circle cx="18" cy="18" r="16" fill="none" stroke="#ccc" stroke-width="2"/><polyline points="21,10 13,18 21,26" fill="none" stroke="#ccc" stroke-width="2"/></svg>
<svg class="arrow" style="left:1110px" width="36" height="36" viewBox="0 0 36 36"><circle cx="18" cy="18" r="16" fill="none" stroke="#ccc" stroke-width="2"/><polyline points="15,10 23,18 15,26" fill="none" stroke="#ccc" stroke-width="2"/></svg>
<p class="quote">Lorem ipsum dolor sit amet, consectetur adipiscing elit, sed do eiusmod tempor incididunt ut labore et dolore magna aliqua. Ut enim ad minim veniam, quis nostrud exercitation ullamco laboris nisi ut aliquip ex ea commodo consequat. Duis aute irure dolor in reprehenderit in voluptate velit esse cillum dolore eu fugiat nulla pariatur. Excepteur sint occaecat cupidatat non proident, sunt in culpa qui officia deserunt mollit anim id est laborum.</p>
<p class="quote-by">Lorem ipsum dolor sit amet, consectetur adipiscing elit, sed do eiusmod</p>

<section class="regions" role="img" aria-label="Red-tinted photo of a business handshake">
  <h2 class="section-title">Ranked amongst the top B2B Lead Generation<br>Companies across the globe</h2>
  <div class="region dark" style="left:133px"><h4>North America</h4><p>Delivery Centre in California<br>Multiple Sales Offices Across US<br>CAN-SPAM Compliant Process<br>End-to-End Event Execution<br>Capabilities</p></div>
  <div class="region light" style="left:447px"><h4>Europe &amp; UK</h4><p>Delivery Centre in UK &amp; Germany<br>Multilingual Lead Generation<br>Capabilities in 20+ Languages<br>GDPR Compliant Process</p></div>
  <div class="region dark" style="left:761px"><h4>APAC</h4><p>Delivery Centre in India<br>Extensive Database of Decision<br>Makers<br>CAN-SPAM Compliant Process</p></div>
</section>

<h2 class="section-title" style="top:3556px">12000+ Leads Generated in Last 10 Months</h2>
<div class="lead" style="left:124px"><b>45%</b><span>North America</span></div>
<div class="lead" style="left:374px"><b>35%</b><span>UK/EMEA</span></div>
<div class="lead" style="left:625px"><b>15%</b><span>North America</span></div>
<div class="lead" style="left:875px"><b>5%</b><span>North America</span></div>

<footer class="site-footer">
  <div class="foot-col" style="left:89px"><h5>ABOUT US</h5><ul><li>About</li><li>Our Team</li><li>Awards</li><li>Our Partnerships</li><li>Our Differentiators</li><li>Locations</li></ul></div>
  <div class="foot-col" style="left:310px"><h5>SERVICES</h5><ul><li>B2B Appointment Setting</li><li>Account Based Marketing</li><li>Research As A Service</li><li>Event / Webinar Management</li><li>Staffing &amp; Talent Acquisition</li><li>Digital Marketing</li><li>Social Media Research</li><li>Lead Nurturing</li></ul></div>
  <div class="foot-col" style="left:604px"><h5>LIBRARY</h5><ul><li>Videos</li><li>Infographics</li><li>Blog</li><li>Case Studies</li></ul></div>
  <div class="foot-col form"><h5>CONTACT US</h5></div>
  <div class="field" style="top:131px">Name</div>
  <div class="field" style="top:179px">Email</div>
  <div class="field" style="top:227px">Phone No</div>
  <div class="field" style="top:275px">Company</div>
  <div class="field" style="top:323px;height:106px">Message</div>
  <a class="btn">Submit</a>
  <p class="copyright">Copyright © 2020 The Company Name. All Rights Reserved.</p>
  <span class="page-code">C28</span>
</footer>

</body>
</html>
```